Motor Oil Lubricant Package Labels

We are looking for a logo and label that we can put on our motor oil bottle 1 liter and 5 liter. The name of our motor oil is Corvana. We want to design our flagship logo for CORVANA MOTOR OILS and as well as the label that will go on the bottle. We have some drafts that we have come up with attached and would like to see more options. The concept of a timeless motor oil and the endless loop of lubricating oils incorporated in the design. We will have full synthetic motor oil, a synthetic blend motor, ATF III transmission fluid, KRL-VI transmission fluid. hydraulic oils etc. Examples will be attached
Target Market(s)
Automotive Lubricants and Chemicals
Industry/Entity Type
Automotive
Logo Text
Corvana Lubricants
Font styles to use
Other font styles liked:
- Let designer choose
Requirements
Must have
- The Corvana sign incorporated in a very cool way to our name. Our brand needs to stick out
Nice to have
- Automotive lubricant related and colors red, white, and blue incorporated in the design
Should not have
- Images of individuals and or topics not related to automotive lubricants.

```html
<!DOCTYPE html>
<html lang="en">
<head>
<meta charset="utf-8">
<title>Corvana Motor Oil Labels</title>
<link rel="stylesheet" href="https://fonts.googleapis.com/css2?family=Oswald:wght@500;600;700&family=Roboto:wght@500;900&display=swap">
<style>
  :root {
    --page: #ebebeb;
    --red: #ec1c24;
    --blue: #2d52a6;
    --ink: #1b1b1b;
    --white: #ffffff;
    --gold: #c99a2e;
  }
  * { box-sizing: border-box; margin: 0; padding: 0; }
  html, body { width: 1200px; height: 935px; overflow: hidden; }
  body {
    background: radial-gradient(ellipse at center, #f7f7f7 0%, var(--page) 75%);
    position: relative;
    font-family: "Oswald", sans-serif;
  }
  .label {
    position: absolute;
    top: 118px;
    width: 432px;
    height: 700px;
    border-radius: 40px;
    overflow: hidden;
    box-shadow: 0 2px 6px rgba(0,0,0,0.18);
    background:
      repeating-linear-gradient(180deg, rgba(255,255,255,0.12) 0 1px, transparent 1px 3px),
      linear-gradient(90deg, #a4a4a4 0%, #f4f4f4 35%, #c9c9c9 60%, #9d9d9d 100%);
  }
  .label--front { left: 142px; }
  .label--back { left: 626px; }
  .label__art { position: absolute; inset: 0; }
  .brand {
    position: absolute;
    font-family: "Roboto", sans-serif;
    font-weight: 900;
    font-size: 60px;
    color: var(--ink);
    letter-spacing: -1px;
    transform: translate(-50%, -50%);
    display: flex;
    align-items: center;
    gap: 10px;
  }
  .brand__dot {
    width: 16px; height: 16px; border-radius: 50%;
    background: var(--blue);
  }
  .label--front .brand { left: 180px; top: 210px; }
  .label--back .brand { left: 148px; top: 178px; }
  .grade {
    position: absolute;
    left: 346px;
    top: 446px;
    transform: translate(-50%, -50%) rotate(-90deg);
    color: var(--white);
    white-space: nowrap;
    text-align: center;
  }
  .label--back .grade { left: 343px; top: 440px; }
  .grade__type {
    font-weight: 600;
    font-size: 22px;
    letter-spacing: 1.5px;
    line-height: 1;
    margin-bottom: 2px;
    padding-right: 30px;
  }
  .grade__main { display: flex; align-items: flex-end; gap: 6px; line-height: 0.85; }
  .grade__sae { font-weight: 700; font-size: 26px; }
  .grade__visc { font-weight: 700; font-size: 82px; letter-spacing: 1px; }
  .grade__api { font-weight: 700; font-size: 32px; margin-left: 6px; }
  .badge {
    position: absolute;
    left: 96px; top: 392px;
    width: 116px; height: 116px;
    transform: translate(-50%, -50%);
    border-radius: 50%;
    background: radial-gradient(circle at 35% 30%, #f6dc8a, var(--gold) 60%, #8a6414);
    display: flex; align-items: center; justify-content: center;
  }
  .badge__inner {
    width: 86px; height: 86px; border-radius: 50%;
    background: var(--white);
    border: 2px solid #b8862a;
    display: flex; align-items: center; justify-content: center;
    text-align: center;
    font-weight: 600; font-size: 12.5px; line-height: 1.35; color: var(--ink);
  }
  .volume {
    position: absolute; left: 40px; top: 648px;
    font-weight: 600; font-size: 22px; color: #2a2a2a;
  }
  .origin {
    position: absolute; left: 203px; top: 650px;
    font-weight: 600; font-size: 18px; color: var(--white);
  }
  .flag {
    position: absolute; left: 42px; top: 584px;
    width: 84px;
    background: var(--white);
  }
  .flag__field {
    height: 26px;
    background: linear-gradient(90deg, #2b3f84 0 40%, transparent 40%),
                repeating-linear-gradient(180deg, #c8202f 0 2px, #ffffff 2px 4px);
  }
  .flag__caption {
    font-family: "Roboto", sans-serif;
    font-weight: 500; font-size: 10px; color: var(--ink);
    text-align: center; padding: 1px 0; letter-spacing: 0.5px;
  }
</style>
</head>
<body>

<section class="label label--front">
  <svg class="label__art" width="432" height="700" viewBox="0 0 432 700" role="img" aria-label="Red and blue flowing band artwork">
    <defs>
      <linearGradient id="flowFront" x1="0" y1="1" x2="0.6" y2="0">
        <stop offset="0" stop-color="#ec1c24"/>
        <stop offset="0.3" stop-color="#2d52a6"/>
        <stop offset="1" stop-color="#2d52a6"/>
      </linearGradient>
      <linearGradient id="capFront" x1="0" y1="0" x2="1" y2="0">
        <stop offset="0" stop-color="#ec1c24"/>
        <stop offset="1" stop-color="#2d52a6"/>
      </linearGradient>
    </defs>
    <rect x="0" y="0" width="432" height="70" fill="url(#capFront)"/>
    <path d="M432,120 L432,700 L200,700 C170,560 220,420 432,120 Z" fill="url(#flowFront)"/>
  </svg>
  <div class="brand">Corvana<span class="brand__dot"></span></div>
  <div class="badge"><div class="badge__inner">FOR<br>GASOLINE<br>ENGINES</div></div>
  <div class="grade">
    <div class="grade__type">SYNTHETIC BLEND</div>
    <div class="grade__main"><span class="grade__sae">SAE</span><span class="grade__visc">5W-30</span><span class="grade__api">APISN</span></div>
  </div>
  <div class="volume">32oz 1946 mL</div>
  <div class="origin">Made In USA</div>
</section>

<section class="label label--back">
  <svg class="label__art" width="432" height="700" viewBox="0 0 432 700" role="img" aria-label="Red and blue flowing band artwork">
    <defs>
      <linearGradient id="flowBack" x1="0" y1="1" x2="0.6" y2="0">
        <stop offset="0" stop-color="#ec1c24"/>
        <stop offset="0.3" stop-color="#2d52a6"/>
        <stop offset="1" stop-color="#2d52a6"/>
      </linearGradient>
      <linearGradient id="capBack" x1="0" y1="0" x2="1" y2="0">
        <stop offset="0" stop-color="#ec1c24"/>
        <stop offset="1" stop-color="#2d52a6"/>
      </linearGradient>
    </defs>
    <rect x="0" y="0" width="432" height="70" fill="url(#capBack)"/>
    <path d="M432,120 L432,700 L200,700 C170,560 220,420 432,120 Z" fill="url(#flowBack)"/>
  </svg>
  <div class="brand">Corvana<span class="brand__dot"></span></div>
  <div class="grade">
    <div class="grade__type">SYNTHETIC BLEND</div>
    <div class="grade__main"><span class="grade__sae">SAE</span><span class="grade__visc">5W-30</span><span class="grade__api">APISN</span></div>
  </div>
  <div class="flag">
    <div class="flag__field" role="img" aria-label="United States flag"></div>
    <div class="flag__caption">MADE IN USA</div>
  </div>
</section>

</body>
</html>
```